Brightfield Ventures Inc. Letterhead

Creation of attractive and eye catching letterhead for a business start-up for the construction industry. Letterhead must relate to construction, but avoid standard hammer and tools in the design.

I forgot to add some details, sorry about that. Some pertinent info: Ph: 916-555-0187 brightfieldventures.example 448 Willowmere Ave, Ste 210 Folsom, CA 95999 info@brightfieldventures.example not sure if slogan should be in there" “Connecting construction professionals to create a purpose driven industry.” must be able to be used in word. Thanks!

```html
<!DOCTYPE html>
<html lang="en">
<head>
<meta charset="utf-8">
<title>Brightfield Ventures Inc. Letterhead</title>
<link href="https://fonts.googleapis.com/css2?family=Open+Sans:wght@400;600;700&display=swap" rel="stylesheet">
<style>
  :root {
    --backdrop: #ececec;
    --paper: #ffffff;
    --brand-red: #c40e12;
    --brand-navy: #1f2a5c;
    --ink: #2a2a2a;
    --rule: #c8c8c8;
  }
  * { box-sizing: border-box; margin: 0; padding: 0; }
  html, body {
    width: 1200px; height: 784px; overflow: hidden;
    background: var(--backdrop);
    font-family: "Open Sans", Arial, sans-serif;
  }
  .canvas {
    width: 1200px; height: 784px;
    display: flex; align-items: center; justify-content: center;
  }
  .letterhead {
    position: relative;
    width: 524px; height: 740px;
    background: var(--paper);
    box-shadow: 0 4px 18px rgba(0,0,0,.12);
    overflow: hidden;
  }
  .top-band {
    position: absolute; top: 30px; left: 0;
    width: 470px; height: 11px;
    background: var(--brand-red);
    border-radius: 0 8px 8px 0;
  }
  .brand {
    position: absolute; top: 78px; right: 48px;
    display: flex; align-items: center; gap: 8px;
  }
  .brand-mark {
    width: 16px; height: 16px; background: var(--brand-red);
  }
  .brand-name {
    font-size: 15px; font-weight: 700; color: var(--brand-navy);
    letter-spacing: .3px;
  }
  .letter-body {
    position: absolute; top: 200px; left: 46px; width: 390px;
    color: var(--ink);
  }
  .salutation {
    font-size: 12px; font-weight: 700; margin-bottom: 12px;
  }
  .letter-body p {
    font-size: 8.6px; line-height: 1.42; margin-bottom: 12px;
  }
  .signature {
    position: absolute; top: 520px; left: 120px;
    width: 110px; height: 44px;
    background: linear-gradient(90deg, #e9e9e9, #f5f5f5);
    border-radius: 4px;
  }
  .footer-rule {
    position: absolute; top: 652px; right: 40px;
    width: 270px; height: 1px; background: var(--rule);
  }
  .footer-address {
    position: absolute; top: 660px; right: 40px;
    font-size: 7.5px; color: var(--ink); text-align: right;
  }
  .footer-contacts {
    position: absolute; top: 675px; right: 40px;
    display: flex; gap: 10px; font-size: 7.5px; color: var(--ink);
  }
  .footer-contacts span { display: inline-flex; align-items: center; gap: 3px; }
  .footer-contacts svg { width: 8px; height: 8px; fill: var(--brand-red); }
  .bottom-band {
    position: absolute; bottom: 26px; right: 0;
    width: 330px; height: 11px;
    background: var(--brand-red);
    border-radius: 8px 0 0 8px;
  }
</style>
</head>
<body>
<main class="canvas">
  <article class="letterhead">
    <div class="top-band"></div>

    <header class="brand">
      <span class="brand-mark"></span>
      <span class="brand-name">Brightfield Ventures Inc.</span>
    </header>

    <section class="letter-body">
      <p class="salutation">Dear Mr. John,</p>
      <p>Lorem Ipsum is simply dummy text of the printing and typesetting industry. Lorem Ipsum has been the industry's standard dummy text ever since the 1500s, when an unknown printer took a galley of type and scrambled it to make a type specimen book. It has survived not only five centuries, but also the leap into electronic typesetting, remaining essentially unchanged.</p>
      <p>The standard chunk of Lorem Ipsum used since the 1500s is reproduced below for those interested. Sections 1.10.32 and 1.10.33 from "de Finibus Bonorum et Malorum" by Cicero are also reproduced in their exact original form, accompanied by English versions from the 1914 translation by H. Rackham</p>
      <p>Lorem Ipsum is simply dummy text of the printing and typesetting industry. Lorem Ipsum has been the industry's standard dummy text ever since the 1500s, when an unknown printer took a galley of type and scrambled it to make a type specimen book. It has survived not only five centuries, but also the leap into electronic typesetting, remaining essentially unchanged. It was popularised in the</p>
      <p>The standard chunk of Lorem Ipsum used since the 1500s is reproduced below for those interested. Sections 1.10.32 and 1.10.33 from "de Finibus Bonorum et Malorum" by Cicero are also reproduced in their exact original form, accompanied by English versions from the 1914 translation by H. Rackham</p>
    </section>

    <div class="signature" role="img" aria-label="Handwritten signature"></div>

    <div class="footer-rule"></div>
    <p class="footer-address">448 Willowmere Ave, Ste 210, Folsom, CA 95999</p>
    <div class="footer-contacts">
      <span><svg viewBox="0 0 10 10"><path d="M2 0.5 L4 2.5 L3 4 Q4.5 6 6 7 L7.5 6 L9.5 8 L8 9.5 Q3 9 0.5 2 Z"/></svg>916-555-0187</span>
      <span><svg viewBox="0 0 10 10"><circle cx="5" cy="5" r="4.5"/></svg>info@brightfieldventures.example</span>
      <span><svg viewBox="0 0 10 10"><circle cx="5" cy="5" r="4.5"/></svg>brightfieldventures.example</span>
    </div>

    <div class="bottom-band"></div>
  </article>
</main>
</body>
</html>
```